Presentation Of Our Epidemiology Consulting Framework

We need a slide deck (png files) for PowerPoint that describes our organization and type of clients we serve, and our 6 phase framework that explains how we work with clients. Please use the minimum amount of text on each slide.  We want a more visual display of how to work with us. We want it to look very similar to our brochure.  We want to also have a few extra branded slides without text that can be used as a template if we decide to add to the deck later or create a new slide deck.
Colors
#56588C
#F28444
#F2E088
#F24C27
#ODODOD

```html
<!DOCTYPE html>
<html lang="en">
<head>
<meta charset="utf-8">
<title>Vantora Health – Consulting Framework Deck</title>
<link rel="stylesheet" href="https://fonts.googleapis.com/css2?family=Montserrat:wght@400;500;600;700;800;900&display=swap">
<style>
  :root{
    --page:#d4d4d6;
    --navy:#2b2858;
    --navy-deep:#221f4a;
    --purple:#56588C;
    --purple-bright:#6a64b6;
    --lavender:#e3e2f1;
    --orange:#F28444;
    --red-orange:#F24C27;
    --gold:#F2E088;
    --ink:#0D0D0D;
    --text:#1f1f24;
    --white:#ffffff;
  }
  *{box-sizing:border-box;margin:0;padding:0}
  html,body{width:1033px;height:1200px;overflow:hidden;background:var(--page)}
  body{position:relative;font-family:"Montserrat",Arial,sans-serif;color:var(--text)}

  .slide{position:absolute;width:475px;height:267px;background:var(--white);overflow:hidden;box-shadow:0 1px 3px rgba(0,0,0,.12)}
  .col-left{left:29px}.col-right{left:532px}
  .row-1{top:32px}.row-2{top:320px}.row-3{top:607px}.row-4{top:895px}

  .photo{position:absolute;top:0;height:267px;width:198px}
  .photo.left{left:0}.photo.right{right:0}
  .photo.team-blue{background:linear-gradient(160deg,#9aa3ad,#5e6570 55%,#d9d4cc)}
  .photo.team-warm{background:linear-gradient(160deg,#b9a58e,#6f5a4a 50%,#c9c1b6)}
  .photo.team-dark{background:linear-gradient(160deg,#cfcfcf,#3b3535 55%,#7a7f86)}
  .photo.lab{background:linear-gradient(160deg,#e7ecef,#b8c5cf 50%,#6c87a6)}

  .badge{position:absolute;width:46px;height:46px;transform:translate(-50%,-50%) rotate(45deg);border-radius:11px;
    background:linear-gradient(135deg,var(--purple-bright),var(--purple));border:2px solid #8d88cf;
    box-shadow:0 3px 8px rgba(30,25,80,.35)}
  .badge-label{position:absolute;transform:translate(-50%,-50%);text-align:center;color:var(--white);line-height:1}
  .badge-label small{display:block;font-size:7px;font-weight:500;letter-spacing:.2px}
  .badge-label b{display:block;font-size:17px;font-weight:800;margin-top:1px}

  .copy{position:absolute}
  .heading{font-size:15px;font-weight:900;line-height:1.2;color:var(--ink);letter-spacing:.3px;text-transform:uppercase}
  .subheading{font-size:10px;font-weight:500;margin-top:11px;color:var(--text);line-height:1.2}
  .steps{list-style:none;margin-top:9px}
  .steps li{position:relative;padding-left:14px;font-size:7.5px;line-height:1.25;margin-bottom:7px;font-weight:500}
  .steps li::before{content:"";position:absolute;left:0;top:1px;width:8px;height:8px;border-radius:50%;background:var(--red-orange)}
  .steps li::after{content:"";position:absolute;left:2px;top:3.5px;width:2.5px;height:2.5px;border-top:1.2px solid #fff;border-right:1.2px solid #fff;transform:rotate(45deg)}

  /* cover + closing */
  .dark{background:linear-gradient(120deg,var(--navy-deep),var(--navy) 60%,#363070)}
  .wordmark{position:absolute;font-size:22px;font-weight:700;color:var(--orange);display:flex;align-items:center;gap:6px;letter-spacing:-.3px}
  .wordmark i{display:block;width:12px;height:12px;border-radius:50%;background:var(--orange)}
  .hero-title{position:absolute;font-size:14.5px;font-weight:900;color:var(--white);line-height:1.12;letter-spacing:.3px}
  .wave{position:absolute;left:0;top:0}
  .hero-portrait{position:absolute;left:277px;top:34px;width:186px;height:186px;border-radius:50%;
    background:linear-gradient(160deg,#c9c6c4,#6c6b77 55%,#2d3550);border:3px solid var(--gold)}
  .intro{position:absolute;left:41px;top:193px;width:200px;font-size:7.5px;line-height:1.5;text-align:justify;color:var(--text)}

  /* why partner */
  .lavender-band{position:absolute;left:336px;top:0;width:139px;height:267px;background:var(--lavender)}
  .partner-title{position:absolute;left:27px;top:21px;font-size:14px}
  .heart{position:absolute;left:232px;top:30px}
  .benefit{position:absolute;left:27px;width:180px}
  .benefit .icon{position:absolute;left:6px;top:2px;width:26px;height:26px;transform:rotate(45deg);border-radius:6px;
    background:linear-gradient(135deg,var(--purple-bright),var(--purple));box-shadow:0 2px 4px rgba(30,25,80,.3)}
  .benefit svg{position:absolute;left:11px;top:7px}
  .benefit h3{margin-left:45px;font-size:8.5px;font-weight:700;color:var(--ink)}
  .benefit p{margin-left:45px;margin-top:4px;font-size:6.3px;line-height:1.35;color:var(--text)}

  .closing-disc{position:absolute;left:281px;top:49px;width:186px;height:186px;border-radius:50%;
    background:radial-gradient(circle at 40% 35%,#433d86,#2b2760);border:3px solid var(--gold)}
  .contact-lead{position:absolute;left:58px;top:187px;font-size:7.5px;line-height:1.4;color:var(--text)}
  .contact-email{position:absolute;left:58px;top:218px}
  .contact-email .icon{position:absolute;left:5px;top:3px;width:24px;height:24px;transform:rotate(45deg);border-radius:6px;background:linear-gradient(135deg,var(--purple-bright),var(--purple))}
  .contact-email svg{position:absolute;left:11px;top:10px}
  .contact-email div{position:absolute;left:46px;top:3px;font-size:8.5px;line-height:1.35;white-space:nowrap;color:var(--ink)}
  .contact-email b{font-weight:700}
</style>
</head>
<body>

<!-- Cover -->
<section class="slide dark col-left row-1">
  <div class="hero-portrait" role="img" aria-label="Portrait of a smiling consultant in a blazer"></div>
  <svg class="wave" width="475" height="267" viewBox="0 0 475 267">
    <defs><linearGradient id="waveGrad" x1="0" x2="1"><stop offset="0" stop-color="#F24C27"/><stop offset=".6" stop-color="#F28444"/><stop offset="1" stop-color="#F24C27"/></linearGradient></defs>
    <path d="M0 238 C8 205 28 183 62 170 C110 152 170 150 218 168 C268 187 295 250 345 250 C405 250 445 205 475 170 L475 267 L0 267Z" fill="#fff"/>
    <path d="M0 238 C8 205 28 183 62 170 C110 152 170 150 218 168 C268 187 295 250 345 250 C405 250 445 205 475 170" fill="none" stroke="url(#waveGrad)" stroke-width="7"/>
    <path d="M440 130 C470 180 455 245 360 255" fill="none" stroke="url(#waveGrad)" stroke-width="9" stroke-linecap="round"/>
  </svg>
  <div class="wordmark" style="left:39px;top:24px"><i></i>Vantora Health</div>
  <h1 class="hero-title" style="left:37px;top:65px">TRANSFORMING HEALTH<br>DATA INTO COMMUNITY<br>IMPACT: THE VANTORA<br>FRAMEWORK</h1>
  <p class="intro">Vantora Health LLC is an epidemiology consulting firm that supports large nonprofit organizations and government agencies that serve black, indigenous, and people of color commonly referred to as BIPOC communities. Our diverse team of innovative</p>
</section>

<!-- Phase 04 -->
<section class="slide col-right row-1">
  <div class="photo right team-warm" role="img" aria-label="Team reviewing frameworks together at a desk"></div>
  <div class="copy" style="left:33px;top:71px">
    <h2 class="heading">Collaborative<br>Refinement</h2>
    <p class="subheading">Ensuring Perfect Alignment</p>
    <ul class="steps">
      <li>Presentation of initial frameworks</li>
      <li>Interactive feedback sessions</li>
      <li>Draft review and optimization</li>
      <li>Stakeholder input integration</li>
    </ul>
  </div>
  <div class="badge" style="left:282px;top:139px"></div>
  <div class="badge-label" style="left:282px;top:139px"><small>PHASE</small><b>04</b></div>
</section>

<!-- Phase 01 -->
<section class="slide col-left row-2">
  <div class="photo left team-blue" role="img" aria-label="Colleagues taking notes around a meeting table"></div>
  <div class="badge" style="left:200px;top:140px"></div>
  <div class="badge-label" style="left:200px;top:140px"><small>PHASE</small><b>01</b></div>
  <div class="copy" style="left:253px;top:61px;width:200px">
    <h2 class="heading">Discovery &amp; Vision<br>Alignment</h2>
    <p class="subheading">Building the Foundation for Success</p>
    <ul class="steps">
      <li>Deep-dive exploration of your organization's unique challenges and opportunities</li>
      <li>Strategic alignment of goals and expectations</li>
      <li>Custom-tailored solution design</li>
      <li>Clear roadmap development with defined milestones</li>
    </ul>
  </div>
</section>

<!-- Phase 05 -->
<section class="slide col-right row-2">
  <div class="photo left team-dark" role="img" aria-label="Three colleagues looking at a tablet"></div>
  <div class="badge" style="left:200px;top:140px"></div>
  <div class="badge-label" style="left:200px;top:140px"><small>PHASE</small><b>05</b></div>
  <div class="copy" style="left:285px;top:67px">
    <h2 class="heading">Impact<br>Delivery</h2>
    <p class="subheading">Bringing Vision to Reality</p>
    <ul class="steps">
      <li>Final deliverable presentation</li>
      <li>Implementation support</li>
      <li>Knowledge transfer</li>
      <li>Impact measurement framework</li>
    </ul>
  </div>
</section>

<!-- Phase 02 -->
<section class="slide col-left row-3">
  <div class="copy" style="left:33px;top:61px">
    <h2 class="heading">Partnership<br>Launch</h2>
    <p class="subheading">Setting the Stage for Excellence</p>
    <ul class="steps">
      <li>Formation of dedicated project team</li>
      <li>Establishment of collaborative workflow</li>
      <li>Comprehensive data gathering</li>
      <li>Strategic timeline planning</li>
      <li>Stakeholder engagement and vision capture</li>
    </ul>
  </div>
  <div class="photo right team-warm" role="img" aria-label="Two colleagues in conversation at a meeting"></div>
  <div class="badge" style="left:282px;top:140px"></div>
  <div class="badge-label" style="left:282px;top:140px"><small>PHASE</small><b>02</b></div>
</section>

<!-- Why partner -->
<section class="slide col-right row-3">
  <div class="lavender-band"></div>
  <h2 class="heading partner-title">Why Partner With Us?</h2>
  <svg class="heart" width="225" height="215" viewBox="0 0 225 215" role="img" aria-label="Two colleagues smiling over a laptop, framed in a heart shape">
    <defs><linearGradient id="heartGrad" x1="0" x2="1" y1="0" y2="1"><stop offset="0" stop-color="#F28444"/><stop offset=".45" stop-color="#c9b8a6"/><stop offset="1" stop-color="#6a64b6"/></linearGradient></defs>
    <path d="M112 210 C60 170 5 130 5 70 C5 30 35 5 65 5 C90 5 105 20 112 38 C119 20 134 5 160 5 C190 5 220 30 220 70 C220 130 165 170 112 210Z" fill="url(#heartGrad)"/>
  </svg>
  <div class="benefit" style="top:51px">
    <div class="icon"></div>
    <svg width="16" height="16" viewBox="0 0 16 16"><ellipse cx="6" cy="6" rx="5" ry="4" fill="#fff"/><ellipse cx="10.5" cy="9.5" rx="4.5" ry="3.5" fill="#fff"/></svg>
    <h3>Expertise</h3>
    <p>Our diverse team of innovative global public health professionals, specialized in epidemiology and health communication</p>
  </div>
  <div class="benefit" style="top:110px">
    <div class="icon"></div>
    <svg width="16" height="16" viewBox="0 0 16 16"><ellipse cx="8" cy="3.5" rx="5" ry="2" fill="#fff"/><path d="M3 5.5v2.5c0 1.1 2.2 2 5 2s5-.9 5-2V5.5c0 1.1-2.2 2-5 2s-5-.9-5-2zm0 4v2.5c0 1.1 2.2 2 5 2s5-.9 5-2V9.5c0 1.1-2.2 2-5 2s-5-.9-5-2z" fill="#fff"/></svg>
    <h3>Impact</h3>
    <p>Proven track record of transforming complex health data into accessible information</p>
  </div>
  <div class="benefit" style="top:162px">
    <div class="icon"></div>
    <svg width="16" height="16" viewBox="0 0 16 16"><circle cx="8" cy="6" r="4.2" fill="#fff"/><rect x="6" y="10" width="4" height="3.5" rx="1" fill="#fff"/></svg>
    <h3>Innovation</h3>
    <p>Custom solutions tailored to BIPOC community needs</p>
  </div>
  <div class="benefit" style="top:209px">
    <div class="icon"></div>
    <svg width="16" height="16" viewBox="0 0 16 16"><rect x="1" y="5" width="4" height="6" rx="1" fill="#fff"/><rect x="11" y="5" width="4" height="6" rx="1" fill="#fff"/><rect x="5" y="6.5" width="6" height="3" rx="1.5" fill="#fff"/></svg>
    <h3>Partnership</h3>
    <p>Collaborative approach ensuring lasting results</p>
  </div>
</section>

<!-- Phase 03 -->
<section class="slide col-left row-4">
  <div class="photo left lab" role="img" aria-label="Researchers working in a laboratory"></div>
  <div class="badge" style="left:200px;top:140px"></div>
  <div class="badge-label" style="left:200px;top:140px"><small>PHASE</small><b>03</b></div>
  <div class="copy" style="left:253px;top:54px;width:210px">
    <h2 class="heading">Expert Execution<br>Where Science<br>Meets Service</h2>
    <p class="subheading" style="margin-top:7px">Our specialized team begins<br>the transformation process:</p>
    <ul class="steps">
      <li>In-depth research and analysis</li>
      <li>Content development and refinement</li>
      <li>Data interpretation and visualization</li>
      <li>Plain language translation of complex health information</li>
    </ul>
  </div>
</section>

<!-- Closing -->
<section class="slide dark col-right row-4">
  <div class="closing-disc"></div>
  <svg class="wave" width="475" height="267" viewBox="0 0 475 267">
    <defs><linearGradient id="waveGrad2" x1="0" x2="1"><stop offset="0" stop-color="#F24C27"/><stop offset=".55" stop-color="#F28444"/><stop offset="1" stop-color="#F24C27"/></linearGradient></defs>
    <path d="M0 228 C12 196 40 173 95 162 C160 150 225 148 282 166 C340 184 378 240 420 237 C445 235 462 220 475 205 L475 267 L0 267Z" fill="#fff"/>
    <path d="M0 228 C12 196 40 173 95 162 C160 150 225 148 282 166 C340 184 378 240 420 237 C445 235 462 220 475 205" fill="none" stroke="url(#waveGrad2)" stroke-width="7"/>
  </svg>
  <div class="wordmark" style="left:39px;top:23px"><i></i>Vantora Health</div>
  <h2 class="hero-title" style="left:39px;top:67px;font-size:15px;line-height:1.27">READY TO TRANSFORM<br>YOUR HEALTH<br>COMMUNICATION?</h2>
  <p class="contact-lead">Contact us to begin your journey toward more<br>effective, equitable health communication.</p>
  <div class="contact-email">
    <div class="icon"></div>
    <svg width="12" height="9" viewBox="0 0 12 9"><rect width="12" height="9" rx="1" fill="#fff"/><path d="M0.5 0.8 6 5 11.5 0.8" fill="none" stroke="#56588C" stroke-width="1.2"/></svg>
    <div>Email<br><b>hello@vantorahealth.com</b></div>
  </div>
</section>

</body>
</html>
```